I am looking for a poster design with a pledge for my clients to take. The pledge will be to not use tanning beds. Our company is a Spray Tanning Salon that focuses on educating our clients on the dangers of indoor tanning while offering a safe alternative through spray tanning. I have an outline of a possible wording but I am VERY open to adjustments on it!
This is not a promotional poster. This is a poster that will be hanging in the salon and our clients will sign around the wall.
Updates

Project Deadline Extended Reason: Not currently in love with any submissions and would like to see more. Looking for a more simple design overall. Added Friday, October 28, 2016

Target Market(s)

Women 20-30 years old

Industry/Entity Type

Salon

Font styles to use
Sans Serif

Requirements
Must have
• Take the pledge to ditch the bed!
• Maple Hollow Tanning
• **Overall simple design, yet eye catching is requested. Not so busy**
Nice to have
• I am open to different wording!
• I pledge to be timeless
• -UVA rays in tanning beds cause wrinkles and other signs of premature aging
• I pledge to be fearless
• -Using tanning beds can cause severe eye damage, a weakened immune system, and melanoma the deadliest form of skin cancer.
• I pledge to be Sunless!
• -Join the GlowWell revolution at Maple Hollow Tanning, Grand Rapids first Sunless Spa Experience.
Should not have
• The photo of the salon on it. I included that photo simply for reference of design, this is where this poster will be hung.

```html
<!DOCTYPE html>
<html lang="en">
<head>
<meta charset="utf-8">
<title>Maple Hollow Tanning Pledge Poster</title>
<link rel="stylesheet" href="https://fonts.googleapis.com/css2?family=Josefin+Sans:wght@300;400&display=swap">
<style>
  :root {
    --backdrop: #efefed;
    --poster-black: #0d0308;
    --poster-plum: #3a0a22;
    --poster-magenta: #c8175a;
    --band-shadow: rgba(70, 18, 42, 0.72);
    --band-magenta: #8c2050;
    --text-white: #ffffff;
    --text-soft: rgba(255, 255, 255, 0.72);
  }
  * { margin: 0; padding: 0; box-sizing: border-box; }
  html, body {
    width: 1200px;
    height: 910px;
    overflow: hidden;
    background: var(--backdrop);
  }
  .canvas {
    position: relative;
    width: 1200px;
    height: 910px;
  }
  .poster {
    position: absolute;
    left: 290px;
    top: 16px;
    width: 620px;
    height: 877px;
    overflow: hidden;
    background: var(--poster-black);
    font-family: "Josefin Sans", sans-serif;
    color: var(--text-white);
  }
  .poster-photo {
    position: absolute;
    inset: 0;
    background:
      radial-gradient(ellipse 30% 42% at 66% 60%, rgba(200, 23, 90, 0.55), transparent 70%),
      radial-gradient(ellipse 20% 28% at 58% 22%, rgba(200, 23, 90, 0.35), transparent 70%),
      linear-gradient(160deg, var(--poster-plum) 0%, #1c0611 45%, var(--poster-black) 100%);
  }
  .poster-band {
    position: absolute;
    top: 0;
    bottom: 0;
  }
  .poster-band--shadow {
    left: 510px;
    width: 76px;
    background: var(--band-shadow);
  }
  .poster-band--magenta {
    left: 586px;
    width: 34px;
    background: var(--band-magenta);
  }
  .brand-name {
    position: absolute;
    left: 28px;
    top: 346px;
    width: 320px;
    font-weight: 300;
    text-transform: uppercase;
    text-align: center;
    line-height: 1;
    white-space: nowrap;
  }
  .brand-name__main {
    display: block;
    font-size: 40px;
    letter-spacing: 0.5px;
  }
  .brand-name__sub {
    display: block;
    margin-top: 12px;
    font-size: 28px;
    letter-spacing: 2px;
  }
  .pledge {
    position: absolute;
    left: 28px;
    top: 540px;
    width: 240px;
  }
  .pledge__headline {
    font-size: 21px;
    font-weight: 400;
    line-height: 1.2;
    text-transform: uppercase;
    letter-spacing: 0.5px;
    margin-bottom: 16px;
  }
  .pledge__list {
    list-style: none;
  }
  .pledge__item {
    margin-bottom: 12px;
  }
  .pledge__vow {
    display: block;
    font-size: 15px;
    font-weight: 400;
    text-transform: uppercase;
    letter-spacing: 1px;
    color: var(--poster-magenta);
    margin-bottom: 3px;
  }
  .pledge__note {
    display: block;
    font-size: 11px;
    font-weight: 300;
    line-height: 1.35;
    color: var(--text-soft);
  }
  .pledge__join {
    margin-top: 6px;
    font-size: 11px;
    font-weight: 400;
    line-height: 1.35;
    color: var(--text-white);
  }
</style>
</head>
<body>
  <main class="canvas">
    <section class="poster">
      <div class="poster-photo" role="img" aria-label="Photograph of a woman's figure in a swimsuit, side view, lit in deep magenta against a dark background"></div>
      <div class="poster-band poster-band--shadow"></div>
      <div class="poster-band poster-band--magenta"></div>
      <h1 class="brand-name">
        <span class="brand-name__main">Maple Hollow</span>
        <span class="brand-name__sub">Tanning</span>
      </h1>
      <div class="pledge">
        <h2 class="pledge__headline">Take the pledge to ditch the bed!</h2>
        <ul class="pledge__list">
          <li class="pledge__item">
            <span class="pledge__vow">I pledge to be timeless</span>
            <span class="pledge__note">UVA rays in tanning beds cause wrinkles and other signs of premature aging.</span>
          </li>
          <li class="pledge__item">
            <span class="pledge__vow">I pledge to be fearless</span>
            <span class="pledge__note">Tanning beds can cause severe eye damage, a weakened immune system, and melanoma, the deadliest form of skin cancer.</span>
          </li>
          <li class="pledge__item">
            <span class="pledge__vow">I pledge to be sunless!</span>
          </li>
        </ul>
        <p class="pledge__join">Join the GlowWell revolution at Maple Hollow Tanning.</p>
      </div>
    </section>
  </main>
</body>
</html>
```